At Home Pet Euthanasia - business cards & brand stationary

We already have a logo and the colors and a website. Need a business card designed that will be able to customized to multiple veterinarians who will be partnering with us. The feel needs to be compassionate, comforting with our tagline 'A Gift of Love at Home'. It will be 2 sides.
On the back our platform/partner vets will be customizing each business card with their own service areas, phone numbers, name and title. On the front, i would like to see experimentation with use of our photos, the logo, tagline and a description 'Peaceful and Compassionate At-Home Pet Euthanasia'

```html
<!DOCTYPE html>
<html lang="en">
<head>
<meta charset="utf-8">
<title>Havenly Pet — Business Card</title>
<link rel="stylesheet" href="https://fonts.googleapis.com/css2?family=Poppins:wght@400;500;600&family=Lato:wght@400;700&display=swap">
<style>
  :root {
    --page-bg: #2b2b2b;
    --brand-blue: #7397c2;
    --brand-blue-dark: #5f84b2;
    --white: #ffffff;
    --photo-grey: #c4c2bf;
    --photo-light: #dcdad7;
    --photo-warm: #e9b3a6;
    --photo-rose: #d98b86;
    --card-shadow: rgba(0, 0, 0, 0.45);
  }
  * { box-sizing: border-box; margin: 0; padding: 0; }
  html, body {
    width: 1200px;
    height: 1015px;
    overflow: hidden;
    background: var(--page-bg);
  }
  .sheet {
    width: 1200px;
    height: 1015px;
    display: flex;
    flex-direction: column;
    align-items: center;
    justify-content: center;
    gap: 20px;
  }
  .card {
    position: relative;
    width: 840px;
    height: 480px;
    overflow: hidden;
    box-shadow: 0 10px 28px var(--card-shadow);
  }

  /* Front */
  .card-front { background: var(--photo-grey); }
  .front-photo {
    position: absolute;
    inset: 0;
    background:
      radial-gradient(ellipse 55% 70% at 28% 78%, var(--photo-warm) 0%, rgba(233,179,166,0) 70%),
      radial-gradient(ellipse 35% 45% at 8% 95%, var(--photo-rose) 0%, rgba(217,139,134,0) 75%),
      linear-gradient(100deg, #bdb9b5 0%, var(--photo-grey) 45%, var(--photo-light) 100%);
  }
  .front-brand {
    position: absolute;
    top: 70px;
    right: 56px;
    width: 420px;
    text-align: left;
  }
  .brand-lockup {
    display: flex;
    align-items: center;
    gap: 16px;
  }
  .brand-mark {
    width: 46px;
    height: 46px;
    border-radius: 50%;
    background: var(--brand-blue);
    flex: none;
  }
  .brand-name {
    font-family: "Poppins", sans-serif;
    font-weight: 600;
    color: var(--brand-blue);
    font-size: 54px;
    line-height: 1;
    letter-spacing: 0.5px;
  }
  .front-description {
    margin-top: 18px;
    font-family: "Poppins", sans-serif;
    font-weight: 500;
    color: var(--white);
    font-size: 21px;
    line-height: 1.25;
    text-align: center;
    letter-spacing: 0.6px;
  }

  /* Back */
  .card-back { background: var(--brand-blue); }
  .back-shape {
    position: absolute;
    inset: 0;
  }
  .holder {
    position: absolute;
    left: 70px;
    top: 100px;
    color: var(--white);
  }
  .holder-name {
    font-family: "Poppins", sans-serif;
    font-weight: 600;
    font-size: 36px;
    line-height: 1.1;
    letter-spacing: 1px;
  }
  .holder-title {
    font-family: "Lato", sans-serif;
    font-size: 22px;
    letter-spacing: 0.5px;
  }
  .contact {
    position: absolute;
    left: 70px;
    bottom: 56px;
    color: var(--white);
    font-family: "Lato", sans-serif;
    font-size: 21px;
    line-height: 1.3;
  }
  .contact-address { margin-bottom: 16px; }
  .contact-list { list-style: none; }
  .contact-list li {
    display: flex;
    align-items: center;
    gap: 12px;
  }
  .contact-list svg {
    width: 20px;
    height: 20px;
    flex: none;
    fill: none;
    stroke: var(--white);
    stroke-width: 1.8;
    stroke-linecap: round;
    stroke-linejoin: round;
  }
  .back-brand {
    position: absolute;
    right: 60px;
    top: 130px;
    width: 300px;
    text-align: center;
  }
  .back-brand .brand-mark {
    width: 84px;
    height: 84px;
    margin: 0 auto 20px;
  }
  .back-brand .brand-name { font-size: 58px; }
  .brand-tagline {
    margin-top: 10px;
    font-family: "Poppins", sans-serif;
    font-weight: 400;
    color: var(--brand-blue);
    font-size: 20px;
    letter-spacing: 0.5px;
  }
</style>
</head>
<body>
<main class="sheet">

  <section class="card card-front">
    <div class="front-photo" role="img" aria-label="Photograph of a girl hugging a blue-eyed cat against a soft grey background"></div>
    <div class="front-brand">
      <div class="brand-lockup">
        <span class="brand-mark"></span>
        <span class="brand-name">Havenly Pet</span>
      </div>
      <p class="front-description">Peaceful and Compassionate<br>At-Home Pet Euthanasia</p>
    </div>
  </section>

  <section class="card card-back">
    <svg class="back-shape" viewBox="0 0 840 480" preserveAspectRatio="none" aria-hidden="true">
      <ellipse cx="680" cy="170" rx="330" ry="300" fill="none" stroke="#ffffff" stroke-width="5"/>
      <ellipse cx="690" cy="160" rx="318" ry="290" fill="#ffffff"/>
    </svg>

    <div class="holder">
      <h1 class="holder-name">Daniel Reyes</h1>
      <p class="holder-title">Managing Director</p>
    </div>

    <div class="contact">
      <p class="contact-address">18 Willow Bend Lane<br>Brookfield, 60513</p>
      <ul class="contact-list">
        <li>
          <svg viewBox="0 0 24 24"><path d="M5 3h4l2 5-2.5 1.5a11 11 0 0 0 6 6L16 13l5 2v4a2 2 0 0 1-2 2A17 17 0 0 1 3 5a2 2 0 0 1 2-2z"/></svg>
          055-208 734 611
        </li>
        <li>
          <svg viewBox="0 0 24 24"><rect x="3" y="5" width="18" height="14" rx="1"/><path d="M3 6l9 7 9-7"/></svg>
          care@havenlypet.example
        </li>
        <li>
          <svg viewBox="0 0 24 24"><circle cx="12" cy="12" r="9"/><path d="M3 12h18M12 3c3 3 3 15 0 18M12 3c-3 3-3 15 0 18"/></svg>
          www.havenlypet.example
        </li>
      </ul>
    </div>

    <div class="back-brand">
      <span class="brand-mark" style="display:block"></span>
      <p class="brand-name">Havenly Pet</p>
      <p class="brand-tagline">A gift of love at home.</p>
    </div>
  </section>

</main>
</body>
</html>
```